I have a logo and need to design the business card and stationery.
Updates

The uploaded logo image named as GREYMARSH CONSTRUCTION which is to be replaced to GREYMARSH CONTRACTS. Kindly add below details and submit the designs- Company name- Greymarsh Engineering Contracts LLP Name & Post- Kelvan Joshi (Designated Partner) Address- Block No.317, Wing C, Tulvo Trade Court, Manek Pural Road, Ruparel Industrial Estate, Goregaon(E), Mumbai - 400 063 Contact- +91 97415 60382 Email- kelvanjoshi@mailbrook.example Website- www.greymarshcontracts.example Contact for Letterhead- +91-22-28754193

Hi Tovin Rahul, We are liking your Design #28860835. We have suggested some changes which are mentioned in feedback. Kindly revert with it asap to finalize this design.

Colors

Designer to choose colors to be used in the design.

```html
<!DOCTYPE html>
<html lang="en">
<head>
<meta charset="utf-8">
<title>Greymarsh Contracts – Business Card</title>
<link rel="stylesheet" href="https://fonts.googleapis.com/css2?family=Exo+2:wght@400;600;700&display=swap">
<style>
  :root {
    --backdrop: #9a9a9a;
    --paper: #ffffff;
    --charcoal: #333333;
    --ink: #3a3a3a;
    --light-text: #f2f2f2;
  }
  * { margin: 0; padding: 0; box-sizing: border-box; }
  html, body {
    width: 1133px;
    height: 1200px;
    overflow: hidden;
    background: var(--backdrop);
    font-family: "Exo 2", sans-serif;
  }
  .card {
    position: absolute;
    overflow: hidden;
  }
  .card-front {
    left: 192px; top: 139px;
    width: 734px; height: 417px;
    background: var(--paper);
  }
  .card-back {
    left: 196px; top: 641px;
    width: 727px; height: 416px;
    background: var(--charcoal);
  }
  .front-band {
    position: absolute;
    left: 0; top: 0;
    width: 734px; height: 417px;
  }
  .brand {
    position: absolute;
    left: 0; width: 100%;
    text-align: center;
    color: var(--ink);
    font-weight: 700;
  }
  .brand-square {
    position: absolute;
    left: 339px; top: 62px;
    width: 56px; height: 56px;
    background: var(--ink);
  }
  .brand-name {
    top: 140px;
    font-size: 28px;
    letter-spacing: 1.5px;
    line-height: 30px;
  }
  .brand-sub {
    top: 171px;
    font-size: 21px;
    font-weight: 400;
    letter-spacing: 9px;
    line-height: 24px;
    padding-left: 9px;
  }
  .holder {
    position: absolute;
    left: 48px; top: 290px;
    width: 360px;
    color: var(--light-text);
  }
  .holder-name {
    font-size: 25px;
    font-weight: 600;
    line-height: 28px;
    letter-spacing: 0.3px;
  }
  .holder-role {
    font-size: 16px;
    line-height: 20px;
  }
  .holder-address {
    margin-top: 6px;
    font-size: 14px;
    line-height: 18px;
  }
  .contacts {
    position: absolute;
    right: 34px; top: 304px;
    list-style: none;
    color: var(--light-text);
    text-align: right;
  }
  .contacts li {
    display: flex;
    justify-content: flex-end;
    align-items: center;
    gap: 10px;
    font-size: 16px;
    line-height: 21px;
    white-space: nowrap;
  }
  .contacts svg {
    width: 14px; height: 14px;
    flex: none;
  }
  .back-square {
    position: absolute;
    left: 333px; top: 118px;
    width: 60px; height: 60px;
    background: var(--paper);
  }
  .back-brand {
    position: absolute;
    left: 0; width: 100%;
    top: 196px;
    text-align: center;
    color: var(--paper);
    font-weight: 700;
    font-size: 27px;
    letter-spacing: 2px;
    line-height: 32px;
  }
  .back-url {
    position: absolute;
    left: 0; width: 100%;
    top: 268px;
    text-align: center;
    color: var(--paper);
    font-size: 16px;
    letter-spacing: 1px;
  }
</style>
</head>
<body>

<section class="card card-front">
  <div class="brand-square"></div>
  <div class="brand brand-name">GREYMARSH</div>
  <div class="brand brand-sub">CONTRACTS</div>

  <svg class="front-band" viewBox="0 0 734 417" aria-hidden="true">
    <polyline points="0,250 107,250 138,277 169,250 734,250" fill="none" stroke="#333333" stroke-width="3"/>
    <polygon points="0,256 110,256 138,282 166,256 734,256 734,417 0,417" fill="#333333"/>
  </svg>

  <div class="holder">
    <div class="holder-name">KELVAN JOSHI</div>
    <div class="holder-role">Designated Partner</div>
    <div class="holder-address">Block No.317, Wing C, Tulvo Trade Court,<br>Manek Pural Road, Ruparel Industrial Estate,<br>Goregaon(E), Mumbai - 400 063</div>
  </div>

  <ul class="contacts">
    <li>+91-22-28754193
      <svg viewBox="0 0 14 14"><path d="M3 1 L5.5 1 L6.3 4 L4.8 5.2 C5.6 7 7 8.4 8.8 9.2 L10 7.7 L13 8.5 L13 11 C13 12 12 13 11 13 C6 12.5 1.5 8 1 3 C1 2 2 1 3 1 Z" fill="#f2f2f2"/></svg>
    </li>
    <li>+91 97415 60382
      <svg viewBox="0 0 14 14"><rect x="3.5" y="0.8" width="7" height="12.4" rx="1.2" fill="none" stroke="#f2f2f2" stroke-width="1.4"/><circle cx="7" cy="11" r="0.8" fill="#f2f2f2"/></svg>
    </li>
    <li>kelvanjoshi@mailbrook.example
      <svg viewBox="0 0 14 14"><rect x="0.5" y="3" width="13" height="9" fill="#f2f2f2"/><polyline points="0.5,3 7,8 13.5,3" fill="none" stroke="#333333" stroke-width="1.2"/></svg>
    </li>
    <li>www.greymarshcontracts.example
      <svg viewBox="0 0 14 14"><circle cx="7" cy="7" r="6.2" fill="#f2f2f2"/><path d="M4 4 Q6 3 7 5 Q6 7 4.5 6.5 Z M8 8 Q10 7.5 11 9 Q9.5 11 8 10.5 Z" fill="#333333"/></svg>
    </li>
  </ul>
</section>

<section class="card card-back">
  <div class="back-square"></div>
  <div class="back-brand">GREYMARSH<br>CONTRACTS</div>
  <div class="back-url">www.greymarshcontracts.example</div>
</section>

</body>
</html>
```